New website for a business that provides STEADY STEPS

A new website that details the services that are provided around STEADY STEPS for people with a disability through QPKV. There also needs to incorporate an about us and a staff page, Plus a referral form that is a google doc.
The business already has a web address that needs to be tailored.
Soft colours are preferred.
Do not have lots of pictures, keep them minimal.
A logo for the business is also needed to be incorporated, and this is a separate project that can be awarded to the website winner.
Website needs to be able to be used on WIX who will be the host for the design.

Target Market(s)

QPKV clients requiring behaviour support clician

Industry/Entity Type

Clinical behaviour support and analysis

Colors
00AB8E
00BBA5
67D7C9
C6EFE9
E9F9F6

Requirements
Must have
• Soft colours, preferable pale turquoise, minimal pictures, clean, sophisticated and classical look

```html
<!DOCTYPE html>
<html lang="en">
<head>
<meta charset="utf-8">
<title>Steady Steps</title>
<link rel="stylesheet" href="https://fonts.googleapis.com/css2?family=Raleway:wght@600;700&family=Roboto:wght@400;500;700&display=swap">
<style>
:root{
  --teal:#00AB8E;
  --teal-2:#00BBA5;
  --teal-3:#67D7C9;
  --mint:#C6EFE9;
  --mist:#E9F9F6;
  --ink:#1a1a1a;
  --body:#555;
  --footer:#1d1d1d;
}
*{box-sizing:border-box;margin:0;padding:0}
html,body{width:1200px;height:4789px;overflow:hidden}
body{font-family:Roboto,Arial,sans-serif;color:var(--ink);background:#fff;position:relative}
.abs{position:absolute}
h2.section-title{font-family:Raleway,Arial,sans-serif;font-weight:700;font-size:36px;text-align:center;position:absolute;left:0;width:100%;letter-spacing:-.3px}
.underline{position:absolute;height:3px;width:64px;background:var(--teal);left:568px}
.btn{position:absolute;background:var(--teal-2);color:#fff;font-weight:700;font-size:14px;border-radius:24px;display:flex;align-items:center;justify-content:center;letter-spacing:.2px}
.body-text{font-size:15px;line-height:28px;color:var(--body)}

/* header */
.site-header{position:absolute;top:0;left:0;width:1200px;height:136px;background:#fff;box-shadow:0 2px 6px rgba(0,0,0,.05)}
.brand{position:absolute;left:112px;top:32px;font-family:Raleway,Arial,sans-serif;font-weight:700;font-size:31px;line-height:40px;color:var(--ink)}
.nav{position:absolute;left:372px;top:64px;display:flex;gap:29px;font-size:13px;font-weight:700}
.nav .active{color:var(--teal)}
.social{position:absolute;display:flex;gap:8px}
.social span{width:28px;height:28px;border-radius:50%;background:#fff;box-shadow:0 2px 6px rgba(0,0,0,.18);display:block;position:relative}
.social span::after{content:"";position:absolute;left:11px;top:11px;width:6px;height:6px;border-radius:50%;background:var(--teal)}

/* hero */
.hero{position:absolute;top:136px;left:0;width:1200px;height:644px;background:linear-gradient(100deg,#3d4a42 0%,#6d7c6a 35%,#b8b4a4 60%,#9fb08a 100%)}
.hero-photo{position:absolute;inset:0}
.hero-copy{position:absolute;left:112px;top:200px;color:#fff}
.hero-copy .kicker{font-family:Raleway,Arial,sans-serif;font-size:21px;font-weight:600}
.hero-copy h1{font-family:Raleway,Arial,sans-serif;font-size:43px;font-weight:700;margin-top:6px}
.hero-copy p{font-size:19px;line-height:31px;font-weight:500;margin-top:14px}
.slider-dots{position:absolute;left:1141px;top:180px;width:8px}
.slider-dots i{display:block;width:6px;height:6px;border-radius:50%;background:#fff;margin:0 auto 26px}
.slider-dots i.on{width:14px;height:14px;margin-left:-4px;background:rgba(255,255,255,.5);border:4px solid #fff}
.scroll-line{position:absolute;left:1143px;top:300px;width:2px;height:66px;background:#fff}
.scroll-label{position:absolute;left:1112px;top:420px;color:#fff;font-size:11px;transform:rotate(90deg);white-space:nowrap}

/* who */
.who{position:absolute;top:780px;left:0;width:1200px;height:572px}
.who .copy{position:absolute;left:126px;width:948px;top:198px;text-align:center}
.who .copy p+p{margin-top:14px}

/* what */
.what{position:absolute;top:1352px;left:0;width:1200px;height:683px;background:var(--mist)}
.service-card{position:absolute;top:170px;width:304px;height:425px;background:#fff;border-radius:6px;box-shadow:0 4px 14px rgba(0,0,0,.1);text-align:center}
.service-card .photo{position:absolute;left:6px;top:6px;right:6px;height:210px;border-radius:4px}
.service-card h3{position:absolute;top:240px;width:100%;font-size:17px;font-weight:700}
.service-card p{position:absolute;top:270px;left:22px;right:22px;font-size:13.5px;line-height:26px;color:var(--body)}
.service-card .more{position:absolute;left:92px;top:362px;width:120px;height:36px;border-radius:18px;background:var(--mist);color:var(--teal);font-size:12px;font-weight:700;display:flex;align-items:center;justify-content:center}
.round-arrow{position:absolute;width:32px;height:32px;border-radius:50%;display:flex;align-items:center;justify-content:center}

/* why */
.why{position:absolute;top:2035px;left:0;width:1200px;height:627px}
.why .photo{position:absolute;left:112px;top:109px;width:488px;height:412px;border-radius:6px;background:linear-gradient(135deg,#7d8c6e,#c9b9a6 45%,#e6c6c6 70%,#8a7ca6)}
.why h2{position:absolute;left:671px;top:130px;font-family:Raleway,Arial,sans-serif;font-size:34px;font-weight:700}
.why .rule{position:absolute;left:671px;top:176px;width:76px;height:3px;background:var(--teal)}
.why .copy{position:absolute;left:673px;top:197px;width:415px;text-align:justify}
.why .copy p+p{margin-top:12px}

/* team */
.team{position:absolute;top:2662px;left:0;width:1200px;height:538px;background:linear-gradient(90deg,#00a98e,#10b9a4 50%,#00a98e)}
.team h2.section-title{color:#fff;top:78px}
.team .underline{background:#fff;top:130px}
.member{position:absolute;top:166px;width:226px;height:257px;border:3px solid #fff;border-radius:4px;box-shadow:0 4px 12px rgba(0,0,0,.2)}
.member .label{position:absolute;left:16px;right:16px;bottom:-5px;height:48px;background:#fff;display:flex;align-items:center;justify-content:center;font-size:17px;font-weight:700}
.member .label.active{color:var(--teal)}

/* clients */
.clients{position:absolute;top:3200px;left:0;width:1200px;height:635px}
.quote-card{position:absolute;left:292px;top:210px;width:714px;height:300px;background:#fff;box-shadow:0 4px 20px rgba(0,0,0,.12)}
.quote-card p{position:absolute;left:140px;top:50px;width:520px;font-size:18px;line-height:30px;color:#666}
.quote-card .who-said{position:absolute;left:140px;top:192px;font-size:21px;font-weight:700}
.quote-card .who-said small{font-size:14px;font-weight:500;color:#555}
.stars{position:absolute;left:140px;top:226px;color:#f0a81c;font-size:15px;letter-spacing:2px}
.avatar-ring{position:absolute;left:192px;top:3453px;width:200px;height:200px;border-radius:50%;background:#fff;box-shadow:0 4px 16px rgba(0,0,0,.12)}
.avatar{position:absolute;left:16px;top:16px;width:168px;height:168px;border-radius:50%;background:linear-gradient(160deg,#9aa3ad,#4b6e96)}

/* contact */
.contact{position:absolute;top:3835px;left:0;width:1200px;height:550px;background:var(--mist)}
.info{position:absolute;top:160px;display:flex;align-items:center;gap:18px}
.info .ico{width:64px;height:64px;border-radius:50%;background:#fff;box-shadow:0 3px 10px rgba(0,0,0,.08);display:flex;align-items:center;justify-content:center}
.info b{display:block;font-size:14px;margin-bottom:6px}
.info span{font-size:13px;color:#444;line-height:19px}
.field{position:absolute;background:#fff;border:1px solid #e2ecea;font-size:14px;color:#444;padding:0 16px;display:flex;align-items:center}

/* footer */
.site-footer{position:absolute;top:4385px;left:0;width:1200px;height:404px;background:var(--footer);color:#fff}
.site-footer .brand{left:112px;top:136px;color:#fff}
.fcol{position:absolute;top:64px}
.fcol h4{font-size:16px;font-weight:700;margin-bottom:16px}
.fcol ul{list-style:none}
.fcol li{font-size:14px;height:50px;position:relative;padding-left:30px;color:#ddd}
.fcol li::before{content:"";position:absolute;left:4px;top:7px;width:5px;height:5px;border-radius:50%;background:var(--teal)}
.fcontact li{padding-left:30px;height:auto;margin-bottom:16px;line-height:20px}
.fcontact li::before{display:none}
.fcontact svg{position:absolute;left:0;top:3px}
.footer-rule{position:absolute;left:112px;right:112px;top:337px;height:1px;background:#3a3a3a}
.copyright{position:absolute;left:437px;top:362px;font-size:13px;color:#ddd}
.site-footer .social{left:982px;top:356px}
.site-footer .social span{background:var(--teal);width:30px;height:30px}
.site-footer .social span::after{background:#fff;left:12px;top:12px}
.site-footer .social span:nth-child(2){background:#fff}
.site-footer .social span:nth-child(2)::after{background:var(--teal)}
</style>
</head>
<body>

<header class="site-header">
  <div class="brand">STEADY<br>STEPS</div>
  <nav class="nav">
    <span class="active">HOME</span><span>ABOUT US</span><span>OUR STAFFS</span><span>SERVICES</span><span>BLOG</span>
  </nav>
  <div class="btn" style="left:819px;top:52px;width:142px;height:42px;font-size:12px">REFER A FRIEND</div>
  <div class="social" style="left:984px;top:60px"><span></span><span></span><span></span></div>
</header>

<section class="hero">
  <div class="hero-photo" role="img" aria-label="Smiling nurse with an older woman in a wheelchair outdoors"></div>
  <div class="hero-copy">
    <div class="kicker">WELCOME TO</div>
    <h1>STEADY STEPS</h1>
    <p>Lorem ipsum dolor sit amet, consectetur adipiscing elit,<br>sed do eiusmod tempor incidea.</p>
  </div>
  <div class="btn" style="left:112px;top:384px;width:148px;height:48px">GET STARTED</div>
  <div class="slider-dots"><i></i><i class="on"></i><i></i><i></i></div>
  <div class="scroll-line"></div>
  <div class="scroll-label">SCROLL DOWN</div>
</section>

<section class="who">
  <h2 class="section-title" style="top:114px">WHO WE ARE</h2>
  <div class="copy body-text">
    <p>Lorem ipsum dolor sit amet, consectetur adipiscing elit, sed do eiusmod tempor incididunt ut labore et dolore magna aliqua. Ut enim ad minim veniam, quis nostrud exercitation ullamco laboris nisi ut aliquip ex ea commodo consequat. Duis aute irure dolor in reprehenderit in cillum dolore eu fugiat nulla pariaturea.</p>
    <p>Lorem ipsum dolor sit amet, consectetur adipiscing elit, sed do eiusmod tempor incididunt ut labore et dolore magna aliqua. Ut enim ad minim veniam, quis nostrud exercitation ullamco laboris nisi ut aliquip ex ea commodo consequat. Duis aute irure dolor in reprehenderit in voluptate velit esse cillum dolore eu fugiat nulla pariatur.</p>
  </div>
  <div class="btn" style="left:526px;top:415px;width:148px;height:48px">LEARN MORE</div>
</section>

<section class="what">
  <h2 class="section-title" style="top:80px">WHAT WE DO</h2>
  <div class="underline" style="top:128px"></div>
  <div class="round-arrow" style="left:35px;top:365px;background:var(--mint)">
    <svg width="12" height="12" viewBox="0 0 12 12"><path d="M7.5 2.5 4 6l3.5 3.5" fill="none" stroke="var(--teal)" stroke-width="2"/></svg>
  </div>
  <div class="round-arrow" style="left:1133px;top:365px;background:var(--teal)">
    <svg width="12" height="12" viewBox="0 0 12 12"><path d="M4.5 2.5 8 6l-3.5 3.5" fill="none" stroke="#fff" stroke-width="2"/></svg>
  </div>

  <article class="service-card" style="left:112px">
    <div class="photo" role="img" aria-label="Young person in a wheelchair laughing with a carer" style="background:linear-gradient(135deg,#7a8f86,#c2b7a1 50%,#e2c8a8)"></div>
    <h3>LOREM IPSUM DOLOR</h3>
    <p>Lorem ipsum dolor sit amet, consectet adipiscing elit, sed do eiusmod tempor incididunt ut laborea.</p>
    <div class="more">READ MORE</div>
  </article>
  <article class="service-card" style="left:448px">
    <div class="photo" role="img" aria-label="Two men talking at a table in a bright room" style="background:linear-gradient(135deg,#cfd6dc,#8b99a3 50%,#5f6d78)"></div>
    <h3>LOREM IPSUM DOLOR</h3>
    <p>Lorem ipsum dolor sit amet, consectet adipiscing elit, sed do eiusmod tempor incididunt ut laborea.</p>
    <div class="more">READ MORE</div>
  </article>
  <article class="service-card" style="left:784px">
    <div class="photo" role="img" aria-label="Nurse holding hands with an older woman" style="background:linear-gradient(135deg,#dfe5e6,#9aabb3 50%,#c8cdcf)"></div>
    <h3>LOREM IPSUM DOLOR</h3>
    <p>Lorem ipsum dolor sit amet, consectet adipiscing elit, sed do eiusmod tempor incididunt ut laborea.</p>
    <div class="more">READ MORE</div>
  </article>
</section>

<section class="why">
  <div class="photo" role="img" aria-label="Carer embracing an older woman in a wheelchair in a garden"></div>
  <h2>WHY CHOOSE US?</h2>
  <div class="rule"></div>
  <div class="copy body-text">
    <p>Lorem ipsum dolor sit amet, consectetur adipiscing elit, sed do eiusmod tempor incididunt ut labore et dolore magna aliqua. Ut enim ad minim veniam, quis nostrud exercitation ullamco laboris nisi utea.</p>
    <p>Lorem ipsum dolor sit amet, consectetur adipiscing elit, sed do eiusmod tempor incididunt ut labore et dolore magna aliqua utenim ad minimea.</p>
  </div>
  <div class="btn" style="left:673px;top:441px;width:150px;height:48px">LEARN MORE</div>
</section>

<section class="team">
  <h2 class="section-title">MEET OUR TEAM</h2>
  <div class="underline"></div>
  <div class="member" style="left:112px;background:linear-gradient(160deg,#e6e6e6,#b9b9b9)" role="img" aria-label="Portrait of a team member">
    <div class="label">LIAM CARTER</div>
  </div>
  <div class="member" style="left:362px;background:linear-gradient(160deg,#f2f2f2,#d9c8b6)" role="img" aria-label="Portrait of a team member">
    <div class="label">NORA HALE</div>
  </div>
  <div class="member" style="left:612px;background:linear-gradient(160deg,#c9c9c9,#8aa5b8 70%,#37a9d6)" role="img" aria-label="Portrait of a team member">
    <div class="label active">LIAM CARTER</div>
  </div>
  <div class="member" style="left:862px;background:linear-gradient(160deg,#ececec,#c9a28c 60%,#d9474f)" role="img" aria-label="Portrait of a team member">
    <div class="label">NORA HALE</div>
  </div>
</section>

<section class="clients">
  <h2 class="section-title" style="top:110px">WHAT OUR CLIENTS SAY</h2>
  <div class="underline" style="top:159px"></div>
  <svg class="abs" style="left:62px;top:337px" width="52" height="34" viewBox="0 0 52 34"><path d="M50 17H4M18 3 4 17l14 14" fill="none" stroke="#333" stroke-width="3"/></svg>
  <svg class="abs" style="left:1086px;top:337px" width="52" height="34" viewBox="0 0 52 34"><path d="M2 17h46M34 3l14 14-14 14" fill="none" stroke="#333" stroke-width="3"/></svg>
  <div class="quote-card">
    <p>Lorem ipsum dolor sit amet, consectetur adipiscing elit, sed do eiusmod tempor incididunt ut labore et dolore magna aliqua. Ut enim ad minim veniam, quis nostrud exercitation ullamco laboris nisi ut aliquipea.</p>
    <div class="who-said">- LIAM CARTER, <small>United States</small></div>
    <div class="stars">★★★★★</div>
    <svg class="abs" style="left:607px;top:192px" width="50" height="40" viewBox="0 0 50 40"><path d="M2 38V20C2 9 8 3 18 2v7c-5 1-7 4-7 9h9v20zM28 38V20c0-11 6-17 16-18v7c-5 1-7 4-7 9h9v20z" fill="#e6e6e6"/></svg>
  </div>
</section>
<div class="avatar-ring"><div class="avatar" role="img" aria-label="Portrait of a client"></div></div>

<section class="contact">
  <h2 class="section-title" style="top:72px">CONTACT US</h2>
  <div class="underline" style="top:121px"></div>

  <div class="info" style="left:184px">
    <div class="ico"><svg width="26" height="26" viewBox="0 0 24 24"><path d="M12 2a6 6 0 0 0-6 6c0 4.5 6 11 6 11s6-6.5 6-11a6 6 0 0 0-6-6zm0 8.2A2.2 2.2 0 1 1 12 5.8a2.2 2.2 0 0 1 0 4.4z" fill="none" stroke="var(--teal)" stroke-width="1.6"/><ellipse cx="12" cy="21" rx="6" ry="1.6" fill="none" stroke="var(--teal)" stroke-width="1.4"/></svg></div>
    <div><b>LOCATION:</b><span>465, Lorum Ipsum Dolore Sed,<br>United States</span></div>
  </div>
  <div class="info" style="left:497px">
    <div class="ico"><svg width="26" height="26" viewBox="0 0 24 24"><path d="M6.6 10.8a15 15 0 0 0 6.6 6.6l2.2-2.2c.3-.3.7-.4 1-.2 1.1.4 2.3.6 3.6.6.6 0 1 .4 1 1V20c0 .6-.4 1-1 1A17 17 0 0 1 3 4c0-.6.4-1 1-1h3.5c.6 0 1 .4 1 1 0 1.3.2 2.5.6 3.6.1.3 0 .7-.2 1z" fill="none" stroke="var(--teal)" stroke-width="1.6"/></svg></div>
    <div><b>CALL US:</b><span>+1 (555) 010 2040</span></div>
  </div>
  <div class="info" style="left:731px">
    <div class="ico"><svg width="26" height="26" viewBox="0 0 24 24"><rect x="3" y="6" width="18" height="13" rx="1.5" fill="var(--teal-3)"/><path d="M3 7l9 6 9-6" fill="none" stroke="#fff" stroke-width="1.6"/></svg></div>
    <div><b>EMAIL US:</b><span>hello@steadysteps.example</span></div>
  </div>

  <div class="field" style="left:165px;top:250px;width:283px;height:50px">Full Name</div>
  <div class="field" style="left:458px;top:250px;width:283px;height:50px">Phone</div>
  <div class="field" style="left:751px;top:250px;width:283px;height:50px">Email Address</div>
  <div class="field" style="left:165px;top:318px;width:869px;height:90px;align-items:flex-start;padding-top:14px">Message</div>
  <div class="btn" style="left:518px;top:426px;width:164px;height:46px">SEND MESSAGE</div>
</section>

<footer class="site-footer">
  <div class="brand">STEADY<br>STEPS</div>
  <div class="fcol" style="left:390px">
    <h4>NAVIGATION</h4>
    <ul><li>Home</li><li>About Us</li><li>Our Staffs</li><li>Services</li><li>Blog</li></ul>
  </div>
  <div class="fcol" style="left:592px">
    <h4>QUICK LINKS</h4>
    <ul><li>Contact Us</li><li>Privacy Policy</li><li>Terms &amp; Conditions</li><li>Disclaimer</li></ul>
  </div>
  <div class="fcol fcontact" style="left:840px">
    <h4>CONTACT US</h4>
    <ul>
      <li><svg width="14" height="14" viewBox="0 0 24 24"><path d="M12 2a7 7 0 0 0-7 7c0 5 7 13 7 13s7-8 7-13a7 7 0 0 0-7-7zm0 9.5A2.5 2.5 0 1 1 12 6.5a2.5 2.5 0 0 1 0 5z" fill="var(--teal)"/></svg>465, Lorum Ipsum Dolore Sed,<br>United States</li>
      <li><svg width="14" height="14" viewBox="0 0 24 24"><path d="M6.6 10.8a15 15 0 0 0 6.6 6.6l2.2-2.2c.3-.3.7-.4 1-.2 1.1.4 2.3.6 3.6.6.6 0 1 .4 1 1V20c0 .6-.4 1-1 1A17 17 0 0 1 3 4c0-.6.4-1 1-1h3.5c.6 0 1 .4 1 1 0 1.3.2 2.5.6 3.6.1.3 0 .7-.2 1z" fill="var(--teal)"/></svg>+1 (555) 010 2040</li>
      <li><svg width="14" height="14" viewBox="0 0 24 24"><rect x="2" y="5" width="20" height="14" rx="1.5" fill="var(--teal)"/><path d="M2 6l10 7 10-7" fill="none" stroke="var(--footer)" stroke-width="1.6"/></svg>hello@steadysteps.example</li>
    </ul>
  </div>
  <div class="footer-rule"></div>
  <div class="copyright">© 2024 Steady Steps &nbsp;|&nbsp; All Rights Reserved</div>
  <div class="social"><span></span><span></span><span></span></div>
</footer>

</body>
</html>
```